Calvanto Group Real Estate Company business cards

New business card design, we are generally happy with the basic layout of the existing front of business card, (feel free to change) but require a head shot photo on the back side.

http://www.calvanto.com.au/

Attached logos, and existing business card

------------------------------

Target Market(s)

Real estate

Industry/Entity Type

Real Estate

Contact Information for Business Card

Standard size double sided

Font styles to use
Other font styles liked:
• Futura

Requirements
Must have
• Photo head shot on the back side
Nice to have
• yes
Should not have
• No

```html
<!DOCTYPE html>
<html lang="en">
<head>
<meta charset="utf-8">
<title>Calvanto Group business cards</title>
<link rel="stylesheet" href="https://fonts.googleapis.com/css2?family=Jost:wght@300;400;500&family=Roboto+Condensed:wght@400;700&display=swap">
<style>
  :root {
    --bg: #e9e9ea;
    --card: #f8f8f9;
    --purple: #3a1f5d;
    --purple-deep: #2b1546;
    --orange: #f08a1c;
    --ink: #2a2340;
    --photo-light: #eef0f4;
    --photo-dark: #27365a;
  }
  * { box-sizing: border-box; margin: 0; padding: 0; }
  html, body { width: 1200px; height: 1200px; overflow: hidden; }
  body {
    background: var(--bg);
    font-family: "Jost", "Futura", sans-serif;
    color: var(--ink);
    position: relative;
  }
  .card {
    position: absolute;
    left: 200px;
    width: 800px;
    height: 457px;
    border-radius: 28px;
    background: var(--card);
    box-shadow: 0 10px 24px rgba(0,0,0,0.12);
    overflow: hidden;
  }
  .card--front { top: 120px; }
  .card--back { top: 623px; }

  /* front */
  .tagline {
    position: absolute;
    left: 70px;
    top: 110px;
    font-size: 40px;
    font-weight: 300;
    line-height: 1.08;
    color: var(--ink);
  }
  .tagline .accent { color: var(--orange); }
  .brand-name {
    position: absolute;
    font-family: "Jost", "Futura", sans-serif;
    font-weight: 400;
    color: var(--purple);
    letter-spacing: 0.5px;
    white-space: nowrap;
  }
  .card--front .brand-name { left: 70px; top: 310px; font-size: 50px; }
  .headshot {
    position: absolute;
    right: 0;
    top: 70px;
    width: 340px;
    height: 387px;
    background: linear-gradient(180deg, var(--photo-light) 0%, #c9ccd6 45%, var(--photo-dark) 100%);
  }

  /* back */
  .card--back .brand-name { left: 70px; top: 80px; font-size: 70px; }
  .person {
    position: absolute;
    left: 74px;
    top: 190px;
  }
  .person__name {
    font-family: "Roboto Condensed", sans-serif;
    font-weight: 700;
    font-size: 28px;
    color: var(--orange);
    letter-spacing: 1px;
  }
  .person__role {
    font-family: "Roboto Condensed", sans-serif;
    font-style: italic;
    font-size: 17px;
    margin-top: 4px;
  }
  .person__abn {
    font-family: "Roboto Condensed", sans-serif;
    font-size: 19px;
    margin-top: 30px;
  }
  .swoosh { position: absolute; inset: 0; }
  .contact {
    position: absolute;
    right: 36px;
    top: 230px;
    list-style: none;
    font-family: "Roboto Condensed", sans-serif;
    font-size: 19px;
    color: #ffffff;
    text-align: right;
  }
  .contact li {
    display: flex;
    justify-content: flex-end;
    align-items: center;
    gap: 12px;
    height: 32px;
  }
  .contact svg { width: 18px; height: 18px; }
</style>
</head>
<body>

<section class="card card--front" aria-label="Business card front">
  <p class="tagline">Let us<br>show you<br><span class="accent">property</span></p>
  <div class="brand-name">calvanto group</div>
  <div class="headshot" role="img" aria-label="Head shot photo of the director in a dark suit and blue tie"></div>
</section>

<section class="card card--back" aria-label="Business card back">
  <svg class="swoosh" viewBox="0 0 800 457" preserveAspectRatio="none" aria-hidden="true">
    <path d="M0,457 L0,425 C220,415 420,340 520,240 C600,160 700,140 800,132 L800,457 Z" fill="var(--purple)"/>
    <path d="M0,410 C230,400 410,320 505,228 C590,145 700,122 800,112" fill="none" stroke="var(--orange)" stroke-width="7"/>
    <path d="M60,418 C260,408 430,330 515,236 C595,152 700,130 800,122" fill="none" stroke="var(--orange)" stroke-width="3"/>
    <path d="M0,457 L0,440 C260,432 500,380 800,300 L800,457 Z" fill="var(--purple-deep)" opacity="0.5"/>
  </svg>

  <div class="brand-name">calvanto group</div>

  <div class="person">
    <p class="person__name">DANIEL TRAN</p>
    <p class="person__role">Director</p>
    <p class="person__abn">ABN: 12 345 678 901</p>
  </div>

  <ul class="contact">
    <li>0412 555 019
      <svg viewBox="0 0 18 18"><rect x="5" y="1" width="8" height="16" rx="2" fill="none" stroke="#fff" stroke-width="1.6"/><circle cx="9" cy="14" r="1" fill="#fff"/></svg>
    </li>
    <li>www.calvanto.com.au
      <svg viewBox="0 0 18 18"><circle cx="9" cy="9" r="7.5" fill="none" stroke="#fff" stroke-width="1.5"/><ellipse cx="9" cy="9" rx="3.2" ry="7.5" fill="none" stroke="#fff" stroke-width="1.2"/><line x1="1.5" y1="9" x2="16.5" y2="9" stroke="#fff" stroke-width="1.2"/></svg>
    </li>
    <li>daniel.tran@calvanto.com.au
      <svg viewBox="0 0 18 18"><rect x="1.5" y="4" width="15" height="10" fill="none" stroke="#fff" stroke-width="1.5"/><path d="M1.5,4 L9,10 L16.5,4" fill="none" stroke="#fff" stroke-width="1.5"/></svg>
    </li>
  </ul>
</section>

</body>
</html>
```